Core Value Graphic for a Service Disabled and Minority Certified contractor

My company, Keystone Aid Partners, is a US Federal Contractor that hires veterans and service disabled veterans. Our website is www.keystoneaid7.example. We work hard to maintain a 50:50 split between veterans and non-veterans on our team. Our tagline is "To Find a Better Way." We are continually looking to integrate technology and efficiency into all that we do.

I want a way to express our company core values visually so that our employees and customers alike can read them and get a sense of who we are, what drives us to succeed, and what makes up our team DNA.

I need an artist like you to help me represent our core values visually. In a manner that I can print it out on an 8"X11" sheet of paper or a large 48" X 48" poster, without losing the visual clarity or that it pixelates out of focus. I am looking for a color scheme that is patriotic with Red, White, and Blues and similar hues. I would also like to incorporate my logo and tagline into the design in some manner.

I have attached several examples of a Core Value Grids from other companies. I am hopeful it will inspire you, and a get your brain juices flowing to provide me with a knockout Core Value Grid that will rock only you can provide! I also include a copy of my company Core Values and a copy of our Logo.

Looking forward to seeing your creations. Thanks.

Target Market(s)

Employees, any potential strategic alliance partners, and customers.

Industry/Entity Type

Contractor

Requirements
Must have
• Patriotic feel and have my logo someplace on the document.

```html
<!DOCTYPE html>
<html lang="en">
<head>
<meta charset="utf-8">
<title>Our Core Values – Keystone Aid Partners</title>
<link href="https://fonts.googleapis.com/css2?family=Montserrat:wght@600;700&family=Open+Sans:wght@400;600;700;800&display=swap" rel="stylesheet">
<style>
  :root{
    --navy:#1c3f78;
    --navy-deep:#132f5c;
    --title-blue:#1d4a8a;
    --red-dark:#9b1c24;
    --red:#c41e2b;
    --grey:#86878a;
    --grey-dark:#68696c;
    --teal:#0f6b92;
    --white:#ffffff;
    --stripe-red:#c0373f;
    --stripe-grey:#c9cacc;
    --stripe-blue:#6b8db3;
  }
  *{margin:0;padding:0;box-sizing:border-box}
  html,body{width:927px;height:1200px;overflow:hidden;background:var(--white)}
  .poster{position:relative;width:927px;height:1200px;overflow:hidden;background:var(--white);font-family:"Open Sans",Arial,sans-serif}

  /* background rules */
  .stripes{position:absolute;left:0;right:0}
  .stripes--red{top:0;height:330px;background:repeating-linear-gradient(to bottom,transparent 0 17px,var(--stripe-red) 17px 20px)}
  .stripes--grey{top:330px;height:380px;background:repeating-linear-gradient(to bottom,transparent 0 17px,var(--stripe-grey) 17px 20px)}
  .stripes--blue{top:710px;height:490px;background:repeating-linear-gradient(to bottom,transparent 0 17px,var(--stripe-blue) 17px 20px)}

  /* title */
  .title-block{position:absolute;left:18px;top:112px;transform:rotate(-16deg);transform-origin:left top;color:var(--title-blue);font-family:"Montserrat",Arial,sans-serif;font-weight:700;line-height:.85;background:var(--white);padding:4px 10px 6px 6px}
  .title-block .title-small{display:block;font-size:50px;letter-spacing:-1px}
  .title-block .title-large{display:block;font-size:104px;letter-spacing:-3px}

  /* value ribbons */
  .values{position:absolute;inset:0;transform:rotate(-16deg);transform-origin:463px 600px}
  .value-band{position:absolute;height:64px;width:1400px;border-top-left-radius:60px;color:var(--white);font-weight:700;font-size:31px;line-height:64px;padding-left:42px;white-space:nowrap;box-shadow:0 6px 10px rgba(0,0,0,.25)}
  .value-column{position:absolute;width:118px;color:var(--white);text-align:center;padding:22px 9px 0;clip-path:polygon(0 0,100% 0,100% 100%,0 calc(100% - 46px));box-shadow:inset -10px 0 14px rgba(0,0,0,.18)}
  .value-column h3{font-family:"Montserrat",Arial,sans-serif;font-weight:700;font-size:17px;line-height:.95;margin:12px 0 4px;letter-spacing:-.3px}
  .value-column h3:first-child{margin-top:0}
  .value-column p{font-size:10.4px;line-height:1.28}

  .value--safety .value-band{left:100px;top:140px;background:linear-gradient(90deg,var(--red-dark),#b3232c 60%,var(--red-dark))}
  .value--safety .value-column{left:100px;top:204px;height:664px;background:linear-gradient(180deg,#a01f27,#8e1a21)}
  .value--wingman .value-band{left:236px;top:212px;background:linear-gradient(90deg,var(--red),#d12432 60%,var(--red))}
  .value--wingman .value-column{left:236px;top:276px;height:686px;background:linear-gradient(180deg,#c41e2b,#ad1a25)}
  .value--fail .value-band{left:372px;top:334px;background:linear-gradient(90deg,#a7a8aa,var(--grey) 60%,#77787b)}
  .value--fail .value-column{left:372px;top:398px;height:667px;background:linear-gradient(180deg,#6f7073,#58595c)}
  .value--boldly .value-band{left:508px;top:424px;background:linear-gradient(90deg,#1a4f88,var(--navy-deep))}
  .value--boldly .value-column{left:508px;top:488px;height:629px;background:linear-gradient(180deg,#137aa3,var(--teal))}
  .value--troops .value-band{left:644px;top:504px;background:linear-gradient(90deg,#24508f,var(--navy))}
  .value--troops .value-column{left:644px;top:568px;height:604px;background:linear-gradient(180deg,#234a85,#17376a)}

  /* brand */
  .brand{position:absolute;left:22px;top:1080px;transform:rotate(-16deg);transform-origin:left top;display:flex;align-items:center;gap:10px}
  .brand-mark{width:26px;height:26px;background:var(--red)}
  .brand-name{font-family:"Open Sans",Arial,sans-serif;font-weight:800;font-size:28px;color:var(--navy);white-space:nowrap}

  /* tagline band */
  .tagline-band{position:absolute;left:40px;top:1170px;width:1100px;height:66px;transform:rotate(-16deg);transform-origin:left top;background:linear-gradient(90deg,var(--navy-deep),var(--navy));color:var(--white);font-family:"Open Sans",Arial,sans-serif;font-weight:700;font-size:38px;line-height:66px;padding-left:36px;white-space:nowrap}
</style>
</head>
<body>
<div class="poster">
  <div class="stripes stripes--red"></div>
  <div class="stripes stripes--grey"></div>
  <div class="stripes stripes--blue"></div>

  <div class="values">
    <section class="value value--safety">
      <div class="value-band">Everyone comes back to the Green Zone.</div>
      <div class="value-column">
        <h3>WHAT IT MEANS</h3>
        <p>Safety takes precedence over every phase of the day’s operation.</p>
        <h3>HOW TO EXPRESS IT</h3>
        <p>Anyone can call a stop to the work in progress if an unsafe act is occurring. In fact, it is each team member’s duty to do so, rectify the unsafe issue, then proceed. Never hesitate; everyone comes back. Finally, each After Action Review begins with discussing safety issues. We always let everyone on the team know of an unsafe situation, so it can be avoided in the future.</p>
        <h3>RESULT</h3>
        <p>All team members go home to their loved ones each day to pursue their individual happiness.</p>
      </div>
    </section>

    <section class="value value--wingman">
      <div class="value-band">Never leave your wingman.</div>
      <div class="value-column">
        <h3>WHAT IT MEANS</h3>
        <p>We always help your team members to be successful. Commitment to each other and to our own personal integrity is the fuel that empowers us.</p>
        <h3>HOW TO EXPRESS IT</h3>
        <p>If a Wingman is having challenges accomplishing their individual priorities or completing their assigned mission, volunteer to help them to do so. This goes for Subs/Suppliers as well. We help those who help us succeed! Always look to establish the best win-win relationship possible, and do what you can to support them if they get into a bind.</p>
        <h3>RESULT</h3>
        <p>Be there for them and they will be there for us.</p>
      </div>
    </section>

    <section class="value value--fail">
      <div class="value-band">Fail quickly and learn.</div>
      <div class="value-column">
        <h3>WHAT IT MEANS</h3>
        <p>If you’re not making mistakes, you’re not taking enough chances or getting out of your comfort zone.</p>
        <h3>HOW TO EXPRESS IT</h3>
        <p>Use your best judgment when trying something new. But, don’t let your pride keep you from saying, <strong>“I was wrong”</strong> when your idea doesn’t work. We trust you will know when it’s time to dump the idea, or stop doing something that doesn’t work.</p>
        <h3>RESULT</h3>
        <p>No one will ever be penalized for making a mistake. Don’t be afraid to try something you believe will work. That’s how we grow ourselves and our team members.</p>
      </div>
    </section>

    <section class="value value--boldly">
      <div class="value-band">Boldly go. Seek. Find.</div>
      <div class="value-column">
        <h3>WHAT IT MEANS</h3>
        <p>We weave innovation into the fabric that makes up our company.</p>
        <h3>HOW TO EXPRESS IT</h3>
        <p>We’re early adopters of technology. We quickly evaluate new technologies or processes that could separate us from our competition. Then we implement and evaluate these new technologies. We dump it quickly if we see it is not helping us achieve “Commander’s Intent”. We have the guts to be first. We iterate continuously and attack, attack, attack.</p>
        <h3>RESULT</h3>
        <p>We will be ahead of our competition. It’s one mechanism that helps us scale. Prosperity favors the bold!</p>
      </div>
    </section>

    <section class="value value--troops">
      <div class="value-band">Troops eat first.</div>
      <div class="value-column">
        <h3>WHAT IT MEANS</h3>
        <p>No leader will put themselves ahead of their subordinates.</p>
        <h3>HOW TO EXPRESS IT</h3>
        <p>We lead by example. Demonstrate the moral courage and discipline to do the right thing at the highest level of quality.</p>
        <h3>RESULT</h3>
        <p>Every new team member will quickly realize their leaders genuinely care for their welfare and success. This is the best way to drive Esprit de Corps and achieve excellence.</p>
      </div>
    </section>
  </div>

  <h1 class="title-block">
    <span class="title-small">OUR</span>
    <span class="title-large">CORE VALUES</span>
  </h1>

  <div class="brand">
    <span class="brand-mark"></span>
    <span class="brand-name">Keystone Aid Partners</span>
  </div>

  <div class="tagline-band">“TO FIND A BETTER WAY”</div>
</div>
</body>
</html>
```